Luxury Wine Label for New Startup Winery

We need a wine label for our new winery startup. We have worked with a local designer but do not feel the resulting label / logo have the elevation required to present our brand as a luxury wine. Our winery is called "Quailbrook Vineyards" and we are focused on extremely high quality hand crafted artisan and estate wines from the Pacific Northwest.
We would like to see designs that utilize a tree line, or other imagery that represents the "Quailbrook" part of our company name. Another interesting feature could be wood grain.
A logo will be required based on your design so please design with this in mind:
This logo should be consistent with the wine bottle label design, and should be representative of our high end exclusive wine while giving a sense of place (Oregon/ Pacific Northwest.)
I will supply an image of the design we received from our local designer, PLEASE NOTE: in general we do like wood grain and tree line concepts but feel the execution was poorly done.
ATTN: Logo design should be suitable for use on: Bottles (Red wine/rose/white wine), Bussiness cards, vehicle signage, business signage, etc
P.S.:
If you have a design that is not outside the box we are still interested in seeing it.
Label is for a burgundy style bottle with a label height of 3.5 - 4" and a width of 3.5-4"
any label <= 4"x4" and >=3.5"x3.5" will be acceptable:
HOWEVER Width should be greater than or equal to height due to the bottle format
Target Market(s)
Wine enthusiasts with adequate discretionary budgets to afford $100 bottles of wine.
Industry/Entity Type
Wine / Winery
Requirements
Must have
- A sense of luxury, a feel of exclusivity, and a theme consistent with our product and brand name
Nice to have
- Tree line, wood grain or other wood themes. Serif fonts
Should not have
- anything cheesy, off topic, hard to read script fonts or anything that makes the label hard to read from a few feet away or too busy

```html
<!DOCTYPE html>
<html lang="en">
<head>
<meta charset="utf-8">
<title>Quailbrook Vineyards — Syrah Label</title>
<link rel="stylesheet" href="https://fonts.googleapis.com/css2?family=IM+Fell+English+SC&display=swap">
<style>
  :root {
    --backdrop: #141316;
    --wood-dark: #2a241f;
    --wood-mid: #4a4038;
    --panel: #060607;
    --gold: #dcbd4f;
    --gold-light: #f1db7a;
    --gold-deep: #a8862c;
  }
  html, body {
    margin: 0;
    padding: 0;
    width: 1200px;
    height: 922px;
    overflow: hidden;
    background: var(--backdrop);
  }
  .canvas {
    position: relative;
    width: 1200px;
    height: 922px;
  }
  .label {
    position: absolute;
    left: 200px;
    top: 61px;
    width: 800px;
    height: 800px;
  }
  .label__wood {
    position: absolute;
    inset: 0;
    background: linear-gradient(90deg, var(--wood-dark), var(--wood-mid) 30%, var(--wood-dark) 55%, var(--wood-mid) 80%, var(--wood-dark));
  }
  .label__panel {
    position: absolute;
    left: 50px;
    top: 50px;
    width: 700px;
    height: 700px;
    box-sizing: border-box;
    background: var(--panel);
    border: 2px solid var(--gold);
    overflow: hidden;
  }
  .label__text {
    position: absolute;
    left: 0;
    width: 100%;
    margin: 0;
    text-align: center;
    font-family: "IM Fell English SC", Georgia, serif;
    color: var(--gold);
    font-weight: 400;
    line-height: 1;
  }
  .winery-name {
    top: 32px;
    font-size: 80px;
    letter-spacing: 0.07em;
    line-height: 76px;
  }
  .vintage {
    top: 213px;
    font-size: 60px;
    font-feature-settings: "onum" 1;
  }
  .region {
    top: 276px;
    font-size: 56px;
    letter-spacing: 0.02em;
  }
  .varietal {
    top: 388px;
    font-size: 44px;
    letter-spacing: 1.1em;
    text-indent: 1.1em;
  }
  .label__scene {
    position: absolute;
    left: 0;
    right: 0;
    bottom: 0;
    height: 245px;
    background: linear-gradient(180deg, var(--panel) 0%, #2a2410 45%, var(--gold-deep) 80%, var(--gold-light) 100%);
  }
</style>
</head>
<body>
  <main class="canvas">
    <section class="label">
      <div class="label__wood" role="img" aria-label="Dark weathered wood grain texture framing the label"></div>
      <div class="label__panel">
        <h1 class="label__text winery-name">Quailbrook<br>Vineyards</h1>
        <p class="label__text vintage">2024</p>
        <p class="label__text region">Willamette Valley</p>
        <p class="label__text varietal">Syrah</p>
        <div class="label__scene" role="img" aria-label="Gold line illustration of a mountain range above a gold foil evergreen tree line"></div>
      </div>
    </section>
  </main>
</body>
</html>
```